Stationery Set for Velmora Company

I need to create full stationery design for my company; Business Cards, Envelops, Letter Heads, Calendar.
In the letter head and Envelops... only contact information and website links.
Our company is a Service Management company with different domains of innovative services including Technology Service Management, Education Services, Outsourcing Management, Events Management.
I need a modern and innovative design specially for the business card. I some transparent designs and I like it, but don't limit your innovation to what I mentioned. Sky is limit for your innovation.

Target Market(s)

Middle East & Africa

Industry/Entity Type

Business Management

Colors
34a7d8
0355a3
85acd3
86cae7
cee9f5
cfdeed
e4daeb
f3f1f8
ecf7fb

Requirements
Must have
• Name, Title, Email, Mobile
Nice to have
• We have multiple locations in USA, KSA, EGY, so I need ideas about how to include all contact details maybe QR / Barcode or something else.
• Please see our locations and contact information: www.brightvelmora.example
Should not have
• Too much text

```html
<!DOCTYPE html>
<html lang="en">
<head>
<meta charset="utf-8">
<title>Velmora Company Stationery Set</title>
<link rel="stylesheet" href="https://fonts.googleapis.com/css2?family=Arimo:wght@400;700&family=Exo+2:wght@500&display=swap">
<style>
  :root {
    --blue-deep: #0355a3;
    --blue-sky: #34a7d8;
    --blue-soft: #85acd3;
    --rule-grey: #5a5d66;
    --paper: #ffffff;
    --backdrop: #f2f2f3;
    --ink: #3a3a3a;
    --band: linear-gradient(90deg, var(--blue-deep) 0%, var(--blue-sky) 55%, var(--blue-deep) 100%);
  }
  * { box-sizing: border-box; margin: 0; padding: 0; }
  html, body { width: 1200px; height: 937px; overflow: hidden; background: var(--backdrop); }
  body { position: relative; font-family: "Arimo", Arial, sans-serif; color: var(--ink); }

  .sheet { position: absolute; background: var(--paper); overflow: hidden; }
  .footer-band { position: absolute; left: 0; bottom: 0; width: 100%; background: var(--band); }
  .footer-rule { position: absolute; left: 0; width: 100%; height: 3px; background: var(--rule-grey); }

  .brand { display: flex; align-items: center; gap: 5px; color: var(--blue-deep); font-weight: 700; white-space: nowrap; }
  .brand-dot { width: 0.7em; height: 0.7em; border-radius: 50%; background: var(--blue-sky); flex: none; }

  /* Letterhead */
  .letterhead { left: 185px; top: 66px; width: 385px; height: 546px; }
  .letterhead .brand { position: absolute; left: 18px; top: 34px; font-size: 15px; }
  .contact-block { position: absolute; right: 18px; top: 24px; text-align: right; font-size: 4.6px; line-height: 6.4px; font-weight: 700; color: #444; font-style: normal; }
  .contact-block .gap { height: 3px; }
  .letter { position: absolute; left: 36px; top: 135px; width: 296px; font-size: 5.1px; line-height: 6.9px; color: #555; }
  .letter p { margin-bottom: 7px; }
  .letter .spacer { height: 14px; }
  .letter strong { color: #333; }
  .signature { display: block; width: 38px; height: 22px; margin: 2px 0 4px; }
  .letterhead .footer-band { height: 30px; }
  .letterhead .footer-rule { bottom: 36px; }

  /* Folder / back sheet */
  .folder { left: 636px; top: 40px; width: 458px; height: 576px; }
  .folder .brand { position: absolute; left: 0; right: 0; top: 292px; justify-content: center; font-size: 27px; }
  .folder .footer-band { height: 34px; }
  .folder .footer-rule { bottom: 41px; }

  /* Business cards */
  .card { left: 45px; width: 177px; height: 100px; border-radius: 7px; }
  .card-front { top: 658px; }
  .card-front .brand { position: absolute; right: 14px; top: 18px; font-size: 9.5px; }
  .card-front .footer-band { height: 52px; }
  .card-front .footer-rule { bottom: 56px; height: 2px; }
  .card-person { position: absolute; left: 10px; top: 64px; color: #fff; font-size: 5.2px; line-height: 6.4px; }
  .card-person .name { font-weight: 700; font-size: 5.6px; }
  .card-person .addr { margin-top: 4px; }
  .card-contacts { position: absolute; right: 10px; top: 64px; color: #fff; font-size: 4.2px; line-height: 5.6px; text-align: right; }
  .card-back { top: 785px; }
  .card-back .brand { position: absolute; left: 0; right: 0; top: 43px; justify-content: center; font-size: 10px; }

  /* Envelopes */
  .envelope { top: 672px; width: 434px; height: 207px; }
  .envelope-front { left: 265px; }
  .envelope-front .brand { position: absolute; left: 16px; top: 26px; font-size: 13px; }
  .envelope-front .footer-band { height: 34px; }
  .envelope-front .footer-rule { bottom: 41px; }
  .envelope-back { left: 736px; width: 432px; }
  .envelope-back .flap { position: absolute; left: 0; top: 0; width: 100%; height: 70px; background: var(--band); border-radius: 0 0 40px 40px; }
  .envelope-back .web { position: absolute; left: 0; right: 0; top: 26px; text-align: center; font-family: "Exo 2", Arial, sans-serif; font-weight: 500; font-size: 12px; letter-spacing: 1.8px; color: #fff; }
</style>
</head>
<body>

<section class="sheet letterhead" aria-label="Letterhead">
  <div class="brand"><span class="brand-dot"></span>Velmora Company</div>
  <address class="contact-block">
    <div>120 Harbor View Road</div>
    <div>Marina District UAE</div>
    <div class="gap"></div>
    <div>044 218 5530</div>
    <div>044 218 5531</div>
    <div class="gap"></div>
    <div>044 218 5532</div>
    <div>info@brightvelmora.example</div>
    <div>www.brightvelmora.example</div>
  </address>
  <div class="letter">
    <p>July 2, 2012</p>
    <p><strong>Dear Client,</strong><br>ABC Building, def St., Country Name</p>
    <p>This is sample filler text for the printing and layout of this letter. It shows how a standard paragraph sits on the page and how lines wrap across the full width of the text block. The words carry no meaning and only stand in for the real message, which will be written later by the sender. It keeps the same length and rhythm as a normal business letter, so spacing and margins can be judged, and it was prepared with desktop publishing software like Pagewright Studio.</p>
    <p>This is sample filler text for the printing and layout of this letter. It shows how a shorter paragraph sits on the page and where the line ends.</p>
    <div class="spacer"></div>
    <p>This is sample filler text for the printing and layout of this letter. It shows how a standard paragraph sits on the page and how lines wrap across the full width of the text block. The words carry no meaning and only stand in for the real message, which will be written later by the sender. It keeps the same length and rhythm as a normal business letter, so spacing and margins can be judged, and it was prepared with desktop publishing software like Pagewright Studio.</p>
    <p>Best Regards,</p>
    <svg class="signature" viewBox="0 0 38 22" aria-hidden="true"><path d="M3 17 C7 4 9 2 8 14 C12 8 15 9 14 15 C18 10 22 11 20 16 L34 14" fill="none" stroke="#333" stroke-width="0.8"/></svg>
    <p style="margin-bottom:0"><strong>Daniel Reyes</strong><br>Director<br><span style="display:block;margin-top:3px">ABC Building, def St., Country Name</span></p>
  </div>
  <div class="footer-rule"></div>
  <div class="footer-band"></div>
</section>

<section class="sheet folder" aria-label="Letterhead back sheet">
  <div class="brand"><span class="brand-dot"></span>Velmora Company</div>
  <div class="footer-rule"></div>
  <div class="footer-band"></div>
</section>

<section class="sheet card card-front" aria-label="Business card front">
  <div class="brand"><span class="brand-dot"></span>Velmora Company</div>
  <div class="footer-rule"></div>
  <div class="footer-band"></div>
  <div class="card-person">
    <div class="name">OMAR HADDAD</div>
    <div>Managing Director</div>
    <div class="addr">120 Harbor View Road<br>Marina District UAE</div>
  </div>
  <div class="card-contacts">
    <div>044 218 5530</div>
    <div>044 218 5531</div>
    <div>omar@brightvelmora.example</div>
    <div>www.brightvelmora.example</div>
  </div>
</section>

<section class="sheet card card-back" aria-label="Business card back">
  <div class="brand"><span class="brand-dot"></span>Velmora Company</div>
</section>

<section class="sheet envelope envelope-front" aria-label="Envelope front">
  <div class="brand"><span class="brand-dot"></span>Velmora Company</div>
  <div class="footer-rule"></div>
  <div class="footer-band"></div>
</section>

<section class="sheet envelope envelope-back" aria-label="Envelope back">
  <div class="flap"></div>
  <div class="web">www.brightvelmora.example</div>
</section>

</body>
</html>
```